Teach English in China Website Redesign Needed

We recruit native English speakers from the US, UK, etc. who want to teach English as a foreign language in schools in China. Our target customer is college educated, age 22-28 and they love to travel. We prefer designs with bright colors and lots of photos. We want to keep all the text on our current homepage, BrightLanternPost.com. We are open to changing our logo. A competitor's page that we like is pinemeadowtutors.com because of their bright colors, photos and use of white space. We are happy to give you a dofollow link and design credit on our homepage. The use of included photos is optional. We need at least a home page design and a standard blog post design.
Target Market(s)
Our target customer is college educated, age 22-28 and they love to travel. Half of our customers are kindergarten teachers. Half of our customers are male.
Logo Text
Bright Lantern Post
Requirements
Must have
- Bright colors
Should not have
- Our homepage must not look crowded. Use white space effectively.

```html
<!DOCTYPE html>
<html lang="en">
<head>
<meta charset="utf-8">
<title>Bright Lantern Post — Teach English in China</title>
<link href="https://fonts.googleapis.com/css2?family=Roboto:wght@400;500;700&family=Open+Sans:ital,wght@0,400;0,600;1,400&display=swap" rel="stylesheet">
<style>
:root{
  --red:#e30613;
  --red-dark:#c4050f;
  --ink:#2b2b2b;
  --text:#555555;
  --grey-box:#8a8a8a;
  --pink-bg:#fdf1f1;
  --light-bg:#efefef;
  --footer:#505050;
  --footer-line:#6a6a6a;
  --white:#ffffff;
}
*{box-sizing:border-box;margin:0;padding:0}
html,body{width:1200px;height:3396px;overflow:hidden}
body{position:relative;background:var(--white);font-family:'Open Sans',sans-serif;color:var(--text)}
.abs{position:absolute}
h1,h2,h3,h4{font-family:'Roboto',sans-serif}

/* header */
.site-header{position:absolute;left:0;top:0;width:1200px;height:147px;border-top:5px solid var(--red)}
.brand{position:absolute;left:100px;top:44px;font-family:'Roboto',sans-serif;font-weight:700;font-size:30px;line-height:32px;color:var(--red);display:flex;align-items:center;gap:12px}
.brand-dot{width:22px;height:22px;background:var(--red);border-radius:50%}
.contact-chip{position:absolute;top:30px;display:flex;align-items:center;gap:12px;font-size:17px;color:var(--ink)}
.chip-icon{width:34px;height:34px;border-radius:50%;display:flex;align-items:center;justify-content:center}
.main-nav{position:absolute;top:98px;left:485px;font-family:'Roboto',sans-serif;font-size:16px;color:var(--ink)}
.main-nav a{position:absolute;white-space:nowrap;color:var(--ink);text-decoration:none}
.main-nav a.active{color:var(--red)}

/* hero */
.hero{position:absolute;left:0;top:147px;width:1200px;height:516px;background:linear-gradient(180deg,#3a3f4a 0%,#5a4a44 45%,#2e3038 100%)}
.hero-photo{position:absolute;inset:0;background:radial-gradient(ellipse at 50% 40%,rgba(150,90,70,.55),rgba(40,44,54,.2) 60%)}
.hero-title{position:absolute;top:178px;width:100%;text-align:center;color:var(--white);font-size:46px;font-weight:500;letter-spacing:.5px}
.hero-sub{position:absolute;top:262px;width:100%;text-align:center;color:var(--white);font-size:19px;line-height:34px}
.hero-btn{position:absolute;left:503px;top:360px;width:194px;height:50px;border:2px solid var(--white);border-radius:25px;background:var(--red);color:var(--white);font-family:'Roboto',sans-serif;font-weight:500;font-size:18px;display:flex;align-items:center;justify-content:center}
.hero-arrow{position:absolute;top:230px}

/* feature strip */
.feature-strip{position:absolute;left:0;top:666px;width:1200px;height:138px;display:flex;gap:3px}
.feature{flex:1;position:relative;color:var(--white)}
.feature.red{background:var(--red)}
.feature.grey{background:var(--grey-box)}
.feature svg{position:absolute;left:22px;top:44px}
.feature h3{position:absolute;left:124px;top:32px;font-size:18px;font-weight:500}
.feature p{position:absolute;left:124px;top:64px;width:260px;font-size:14.5px;line-height:24px}

/* highlights */
.section-title{font-size:27px;font-weight:500;color:var(--red)}
.highlights-title{position:absolute;left:100px;top:868px}
.highlight-list{position:absolute;left:100px;top:940px;list-style:none;font-size:15.5px;color:#333;line-height:28px;width:600px}
.highlight-list li{position:relative;padding-left:26px}
.highlight-list li::before{content:"";position:absolute;left:0;top:9px;width:10px;height:10px;border:2.5px solid var(--red);border-radius:50%}
.easel{position:absolute;left:804px;top:872px;width:260px;height:408px;background:linear-gradient(180deg,#2a2a2a 0%,#2a2a2a 45%,#9a6b45 46%,#7c5535 100%);border-radius:6px}

/* job description */
.job-band{position:absolute;left:0;top:1320px;width:1200px;height:518px;background:var(--pink-bg)}
.centered-title{position:absolute;width:100%;text-align:center}
.title-rule{position:absolute;left:570px;width:60px;height:2px;background:var(--red)}
.job-sub{position:absolute;top:1442px;width:100%;text-align:center;font-size:15.5px;color:#333}
.req{position:absolute;top:1515px;width:200px;text-align:center}
.req svg{display:block;margin:0 auto}
.req p{margin-top:16px;font-size:15.5px;line-height:26px;color:#333}

/* blog */
.blog-card{position:absolute;top:1992px;width:303px;height:419px;border:1px solid #e2e2e2;background:var(--white)}
.blog-photo{height:215px}
.blog-card h4{margin:26px 13px 0;font-size:16.5px;font-weight:500;color:var(--ink)}
.blog-card p{margin:8px 13px 0;font-size:14px;line-height:22px;color:#555}
.btn-outline{position:absolute;left:13px;top:356px;width:106px;height:43px;border:1px solid #bbb;border-radius:3px;font-size:15px;color:#333;display:flex;align-items:center;justify-content:center;background:var(--white)}
.btn-outline.filled{background:var(--red);border-color:var(--red);color:var(--white)}

/* testimonials */
.testimonial-band{position:absolute;left:0;top:2484px;width:1200px;height:477px;background:var(--light-bg)}
.quote-box{position:absolute;top:2626px;width:308px;height:181px;border:1.5px solid #999;border-radius:6px;background:var(--white);padding:22px 22px 0 52px;font-family:'Open Sans',sans-serif;font-style:italic;font-size:13.5px;line-height:24px;color:#666}
.quote-box.featured{background:var(--red);border-color:var(--red);color:var(--white)}
.quote-mark{position:absolute;left:16px;top:10px;font-family:'Roboto',sans-serif;font-style:normal;font-weight:700;font-size:48px;line-height:48px;color:#555}
.quote-box.featured .quote-mark{color:var(--white)}
.quote-tail{position:absolute;left:18px;bottom:-14px;width:0;height:0;border-left:14px solid transparent;border-right:14px solid transparent;border-top:14px solid #999}
.quote-box.featured .quote-tail{border-top-color:var(--red)}
.author{position:absolute;top:2825px;display:flex;align-items:center;gap:16px}
.avatar{width:64px;height:64px;border-radius:50%;border:3px solid var(--red);background:radial-gradient(circle at 50% 40%,#b48d76,#4b3a33)}
.author h4{font-size:16px;font-weight:500;color:var(--ink)}
.author span{font-size:12.5px;color:#888}

/* footer */
.site-footer{position:absolute;left:0;top:2961px;width:1200px;height:435px;background:var(--footer);color:var(--white)}
.footer-brand{position:absolute;left:100px;top:190px;font-family:'Roboto',sans-serif;font-weight:700;font-size:28px;line-height:34px;color:var(--white)}
.footer-col h4{position:absolute;top:78px;font-size:17px;font-weight:500;letter-spacing:.5px}
.footer-col .rule{position:absolute;top:110px;height:2px;background:#bbb}
.quick-links{position:absolute;left:367px;top:130px;list-style:none;font-size:14.5px;line-height:30px}
.contact-item{position:absolute;left:543px;display:flex;gap:14px}
.contact-icon{width:34px;height:34px;border-radius:50%;background:var(--white);flex:none;display:flex;align-items:center;justify-content:center}
.contact-item strong{font-family:'Roboto',sans-serif;font-weight:500;font-size:14.5px;display:block}
.contact-item span{font-size:13.5px;line-height:22px;color:#e6e6e6}
.field{position:absolute;border:1.5px solid #ddd;font-size:11px;color:#eee;padding:7px 8px}
.send-btn{position:absolute;left:815px;top:242px;width:117px;height:38px;background:var(--red);border:1.5px solid var(--white);font-size:12px;display:flex;align-items:center;justify-content:center}
.footer-rule{position:absolute;left:100px;top:356px;width:1000px;height:1px;background:var(--footer-line)}
.copyright{position:absolute;left:100px;top:384px;font-size:13.5px;color:#e6e6e6}
.social{position:absolute;top:372px;width:34px;height:34px;border:2px solid var(--white);border-radius:50%}
</style>
</head>
<body>

<header class="site-header">
  <div class="brand"><span class="brand-dot"></span>Bright Lantern Post</div>
  <div class="contact-chip" style="left:666px">
    <span class="chip-icon" style="background:var(--red)"><svg width="18" height="14" viewBox="0 0 18 14"><rect x="1" y="1" width="16" height="12" rx="1" fill="none" stroke="#fff" stroke-width="2"/><path d="M1 1l8 7 8-7" fill="none" stroke="#fff" stroke-width="2"/></svg></span>
    mara@brightlanternpost.com
  </div>
  <div class="contact-chip" style="left:958px">
    <span class="chip-icon" style="background:#1f2a3a"><svg width="16" height="16" viewBox="0 0 16 16"><path d="M3 1l3 1 1 4-2 1a9 9 0 0 0 4 4l1-2 4 1 1 3-2 2C7 15 1 9 1 3z" fill="#fff"/></svg></span>
    555-318-4072
  </div>
  <nav class="main-nav">
    <a class="active" style="left:0">HOME</a>
    <a style="left:110px">AVAILABLE JOBS</a>
    <a style="left:303px">APPLY ONLINE</a>
    <a style="left:477px">BLOG</a>
    <a style="left:584px">FAQ</a>
  </nav>
</header>

<section class="hero">
  <div class="hero-photo" role="img" aria-label="Photo of a traditional Chinese tower lit at dusk above city traffic"></div>
  <svg class="hero-arrow" style="left:22px" width="30" height="56" viewBox="0 0 30 56"><path d="M26 2L4 28l22 26" fill="none" stroke="#fff" stroke-width="3"/></svg>
  <svg class="hero-arrow" style="left:1148px" width="30" height="56" viewBox="0 0 30 56"><path d="M4 2l22 26L4 54" fill="none" stroke="#fff" stroke-width="3"/></svg>
  <h1 class="hero-title">TEACH ENGLISH IN CHINA</h1>
  <p class="hero-sub">A Bachelor's degree and experience is recommended, but a degree<br>is not required to teach kindergarten.</p>
  <div class="hero-btn">START WITH US</div>
</section>

<section class="feature-strip">
  <div class="feature red">
    <svg width="76" height="50" viewBox="0 0 76 50"><path d="M38 4L2 18l36 14 36-14z" fill="#fff"/><path d="M16 25v13c0 5 10 9 22 9s22-4 22-9V25L38 34z" fill="#fff"/><path d="M70 20v18" stroke="#fff" stroke-width="3"/></svg>
    <h3>JOB REQUIREMENTS</h3>
    <p>5-day work week, 25 hours teaching per week plus some office hours.</p>
  </div>
  <div class="feature grey">
    <svg width="60" height="54" viewBox="0 0 60 54"><rect x="20" y="4" width="36" height="26" fill="none" stroke="#fff" stroke-width="3"/><circle cx="10" cy="18" r="6" fill="#fff"/><path d="M2 44V30h16l10-6v6l-10 6v8z" fill="#fff"/><circle cx="30" cy="44" r="5" fill="#fff"/><circle cx="46" cy="44" r="5" fill="#fff"/></svg>
    <h3>WHAT WE OFFER</h3>
    <p>5-day work week, 25 hours teaching per week plus some office hours.</p>
  </div>
  <div class="feature red">
    <svg width="52" height="56" viewBox="0 0 52 56"><rect x="6" y="3" width="36" height="48" rx="2" fill="none" stroke="#fff" stroke-width="3"/><path d="M13 14h22M13 22h22M13 30h14" stroke="#fff" stroke-width="3"/><circle cx="38" cy="42" r="9" fill="#fff"/></svg>
    <h3>PRIVATE ENGLISH</h3>
    <p>5-day work week, 25 hours teaching per week plus some office hours.</p>
  </div>
</section>

<h2 class="section-title highlights-title">Our Highlights</h2>
<ul class="highlight-list">
  <li>Competitive compensation: 7000-9000 RMB/month, up to 18,000 RMB (divide by 6.5 for US dollars) if you have a bachelor's degree, 2+ years of teaching experience</li>
  <li>Housing allowance: 2000 RMB/month (housing is cheaper in China)</li>
  <li>Teach private English lessons after work for 250 RMB/hr ($38 US per hour)</li>
  <li>Airfare reimbursement: 5000 RMB at end of completed 1 year contract</li>
  <li>Free TESOL / TEFL training and certification</li>
  <li>Invitation letter so you can apply for a visa (Z visa if you have a bachelor's degree).</li>
  <li>Airport pickup</li>
  <li>5-day work week, 25 hours teaching per week plus some office hours</li>
  <li>20 paid holidays</li>
  <li>Free Chinese classes 2 hours per week with most jobs</li>
</ul>
<div class="easel" role="img" aria-label="Illustration of a chalkboard on a wooden easel"></div>

<section class="job-band"></section>
<h2 class="section-title centered-title" style="top:1360px">Job Description</h2>
<div class="title-rule" style="top:1410px"></div>
<p class="job-sub">General Job Requirements (See our current job openings for details on all jobs.)</p>

<div class="req" style="left:92px">
  <svg width="140" height="160" viewBox="0 0 140 160"><path d="M70 150l-14-14A66 66 0 1 1 84 136z" fill="#fff" stroke="#444" stroke-width="3"/><circle cx="52" cy="62" r="9" fill="#444"/><circle cx="88" cy="62" r="9" fill="#444"/><circle cx="70" cy="56" r="10" fill="#444"/><path d="M36 90a16 14 0 0 1 32 0zM72 90a16 14 0 0 1 32 0zM52 88a18 16 0 0 1 36 0z" fill="#444"/></svg>
  <p>Must be at least 18 years<br>old</p>
</div>
<div class="req" style="left:303px">
  <svg width="140" height="160" viewBox="0 0 140 160"><path d="M70 150l-14-14A66 66 0 1 1 84 136z" fill="var(--red)"/><circle cx="70" cy="54" r="16" fill="#fff"/><path d="M40 104a30 30 0 0 1 60 0z" fill="#fff"/><path d="M58 40h24v8H58z" fill="#222"/></svg>
  <p>High School Diploma or<br>equivalent</p>
</div>
<div class="req" style="left:507px">
  <svg width="140" height="160" viewBox="0 0 140 160"><path d="M70 150l-14-14A66 66 0 1 1 84 136z" fill="#fff" stroke="#444" stroke-width="3"/><rect x="58" y="40" width="46" height="32" fill="none" stroke="#444" stroke-width="3"/><circle cx="44" cy="56" r="7" fill="#444"/><path d="M34 92V72h18l10-6v7l-10 6v13z" fill="#444"/><circle cx="72" cy="90" r="7" fill="#444"/><circle cx="94" cy="90" r="7" fill="#444"/></svg>
  <p>Speak, read, and write English<br>fluently</p>
</div>
<div class="req" style="left:715px">
  <svg width="140" height="160" viewBox="0 0 140 160"><path d="M70 150l-14-14A66 66 0 1 1 84 136z" fill="#fff" stroke="#444" stroke-width="3"/><rect x="38" y="40" width="64" height="44" fill="none" stroke="#444" stroke-width="3"/><path d="M60 96h20M70 84v12" stroke="#444" stroke-width="3"/><path d="M62 70l20-20 6 6-20 20h-6z" fill="#444"/></svg>
  <p>Hands-on teaching<br>experience preferred but<br>not required</p>
</div>
<div class="req" style="left:919px">
  <svg width="140" height="160" viewBox="0 0 140 160"><path d="M70 150l-14-14A66 66 0 1 1 84 136z" fill="#fff" stroke="#444" stroke-width="3"/><path d="M70 32l-22 9 22 9 22-9z" fill="#444"/><circle cx="70" cy="60" r="10" fill="#444"/><path d="M44 100V78l26 8 26-8v22l-26 8z" fill="#444"/></svg>
  <p>Excellent verbal<br>communication skills</p>
</div>

<h2 class="section-title centered-title" style="top:1892px">Recent Blog Posts</h2>
<div class="title-rule" style="top:1942px"></div>

<article class="blog-card" style="left:100px">
  <div class="blog-photo" role="img" aria-label="Photo of children at a classroom table" style="background:linear-gradient(135deg,#d9d3cc,#c2323a 60%,#e9e4df)"></div>
  <h4>Basic Chinese Greetings</h4>
  <p>Chinese is a pretty difficult language for English speakers to learn compared to Spanish or French.</p>
  <div class="btn-outline">Read More</div>
</article>
<article class="blog-card" style="left:448px">
  <div class="blog-photo" role="img" aria-label="Photo of students in uniform standing in rows" style="background:linear-gradient(180deg,#8b8e86,#3f3e44 55%,#a8aaa3)"></div>
  <h4>How China Can Get Enough English...</h4>
  <p>Chinese is a pretty difficult language for English speakers to learn compared to Spanish or French.</p>
  <div class="btn-outline filled">Read More</div>
</article>
<article class="blog-card" style="left:797px">
  <div class="blog-photo" role="img" aria-label="Photo of a teacher hugging a group of children" style="background:linear-gradient(135deg,#6b8f3a,#c9762f 50%,#3a5ea5)"></div>
  <h4>What are ESOL, EFL, ESL, ESP?</h4>
  <p>Chinese is a pretty difficult language for English speakers to learn compared to Spanish or French.</p>
  <div class="btn-outline">Read More</div>
</article>

<section class="testimonial-band"></section>
<h2 class="section-title centered-title" style="top:2526px">Testimonials</h2>
<div class="title-rule" style="top:2576px"></div>

<blockquote class="quote-box" style="left:100px"><span class="quote-mark">“</span>Mara was extremely helpful during the entire process. Moving to another country is a very challenging ordeal and having someone like Mara on your side makes all the difference.<span class="quote-tail"></span></blockquote>
<blockquote class="quote-box featured" style="left:448px"><span class="quote-mark">“</span>When I began my search for a teaching job in China, I had no idea what to expect. Luckily, I came across Mara with BrightLanternPost.com. Not only did Mara.<span class="quote-tail"></span></blockquote>
<blockquote class="quote-box" style="left:795px"><span class="quote-mark">“</span>As soon as we got in touch, Mara guided me through every step of the process. I have had THE BEST experience under her guidance. Mara has been amazing at finding the best jobs.<span class="quote-tail"></span></blockquote>

<div class="author" style="left:100px"><div class="avatar" role="img" aria-label="Portrait photo of the reviewer"></div><div><h4>Theo Lindqvist</h4><span>January 2, 2017</span></div></div>
<div class="author" style="left:448px"><div class="avatar" role="img" aria-label="Portrait photo of the reviewer"></div><div><h4>Priya Wexford</h4><span>December 20, 2016</span></div></div>
<div class="author" style="left:795px"><div class="avatar" role="img" aria-label="Portrait photo of the reviewer"></div><div><h4>Carmen Ostrava</h4><span>December 21, 2016</span></div></div>

<footer class="site-footer">
  <div class="footer-brand">Bright Lantern<br>Post</div>

  <div class="footer-col"><h4 style="left:367px">QUICK LINKS</h4><div class="rule" style="left:367px;width:108px"></div></div>
  <ul class="quick-links">
    <li>› Home</li><li>› Available Jobs</li><li>› Apply Online</li><li>› Blog</li><li>› FAQ</li>
  </ul>

  <div class="footer-col"><h4 style="left:543px">CONTACT US</h4><div class="rule" style="left:543px;width:110px"></div></div>
  <div class="contact-item" style="top:132px">
    <span class="contact-icon"><svg width="14" height="18" viewBox="0 0 14 18"><path d="M7 17S1 10 1 6.5a6 6 0 0 1 12 0C13 10 7 17 7 17z" fill="#505050"/><circle cx="7" cy="6.5" r="2.2" fill="#fff"/></svg></span>
    <div><strong>ADDRESS,</strong><span>418 Willow Heron Ln<br>Maple Ridge, Oregon</span></div>
  </div>
  <div class="contact-item" style="top:218px">
    <span class="contact-icon"><svg width="16" height="16" viewBox="0 0 16 16"><path d="M3 1l3 1 1 4-2 1a9 9 0 0 0 4 4l1-2 4 1 1 3-2 2C7 15 1 9 1 3z" fill="#505050"/></svg></span>
    <div><strong>PHONE:</strong><span>555-318-4072</span></div>
  </div>
  <div class="contact-item" style="top:280px">
    <span class="contact-icon"><svg width="16" height="12" viewBox="0 0 18 14"><rect x="1" y="1" width="16" height="12" fill="none" stroke="#505050" stroke-width="2"/><path d="M1 1l8 7 8-7" fill="none" stroke="#505050" stroke-width="2"/></svg></span>
    <div><strong>Mail:</strong><span>mara@brightlanternpost.com</span></div>
  </div>

  <div class="footer-col"><h4 style="left:815px">CONTACT FORM</h4><div class="rule" style="left:815px;width:144px"></div></div>
  <div class="field" style="left:815px;top:128px;width:142px;height:38px">Name</div>
  <div class="field" style="left:961px;top:128px;width:139px;height:38px">Phone</div>
  <div class="field" style="left:815px;top:174px;width:285px;height:64px">Message</div>
  <div class="send-btn">SEND MESSAGE</div>

  <div class="footer-rule"></div>
  <p class="copyright">Copyright © 2017 Bright Lantern Post. All Right Reserved</p>
  <span class="social" style="left:951px"></span>
  <span class="social" style="left:993px"></span>
  <span class="social" style="left:1035px"></span>
  <span class="social" style="left:1077px"></span>
</footer>

</body>
</html>
```